Very visible CoWorking Building Sign overlooking downtown LA and 110 freeway

Our building is drab but very visible and in the best location. We need a great sign for our monolith that overlooks downtown LA and the 100 freeway. We are a new CoWorking business and would like to have a few things we do on the sign: private offices, virtual offices, CoWorking Lounge. Everything we have seen is ho-hum. Can you get us noticed? We need people to know what we do and that we are here but in a creative, professional, unique sign.
Target Market(s)
People who have a business in DTLA, remote workers and those who work from home who need a professional address.
Requirements
Must have
- Our logo (which can be somewhat reimagined) which has our address 2417 on it. The three things we focus on: Private Offices, Virtual Offices, CoWorking Lounge. Incorporate some Navy. Readable from several hundred feet away.
Nice to have
- Mural feel? Something inspirational in this crazy COVID times? Graphics? Color block. I like the idea of decorative but it has to be readable as a building sign. The same with the use of colors. Our colors are grays and navy but with a pop of the chartreuse (we have 2 velvet chartreuse chairs in the space). Helpful to view our website: Harborview2417.com.
Should not have
- Not too graffiti. Keep it professional but unique and wow.

```html
<!DOCTYPE html>
<html lang="en">
<head>
<meta charset="utf-8">
<title>Harborview 2417 Building Sign</title>
<link rel="stylesheet" href="https://fonts.googleapis.com/css2?family=Josefin+Sans:wght@300&family=Tinos:wght@700&display=swap">
<style>
  :root {
    --backdrop: #c4c4c4;
    --navy: #0d2a4f;
    --chartreuse: #8dc63f;
    --blue: #0864ad;
    --white: #ffffff;
  }
  html, body {
    margin: 0;
    padding: 0;
    width: 1200px;
    height: 1097px;
    overflow: hidden;
    background: var(--backdrop);
  }
  .sign {
    position: absolute;
    left: 300px;
    top: 48px;
    width: 600px;
    height: 1000px;
    display: block;
  }
  .brand-name {
    font-family: "Josefin Sans", sans-serif;
    font-weight: 300;
    fill: var(--white);
  }
  .service-label {
    font-family: "Tinos", serif;
    font-weight: 700;
    font-size: 38px;
    letter-spacing: 1px;
    fill: var(--white);
  }
  .phone-number {
    font-family: "Tinos", serif;
    font-weight: 700;
    fill: var(--white);
  }
</style>
</head>
<body>
<svg class="sign" viewBox="0 0 600 1000" xmlns="http://www.w3.org/2000/svg">
  <rect class="sign-field" x="0" y="0" width="600" height="1000" fill="var(--navy)"/>

  <text class="brand-name" x="40" y="150" font-size="78" textLength="520" lengthAdjust="spacingAndGlyphs">HARBORVIEW2417.com</text>
  <rect class="brand-rule" x="245" y="206" width="110" height="7" fill="var(--white)"/>

  <g class="service service-private">
    <circle cx="151" cy="323" r="83" fill="var(--chartreuse)" stroke="var(--white)" stroke-width="2" role="img" aria-label="Line icon of a desk with chair, lamp and framed picture"/>
    <text class="service-label" x="261" y="311">PRIVATE</text>
    <text class="service-label" x="261" y="354">OFFICES</text>
  </g>
  <line class="service-divider" x1="276" y1="417" x2="449" y2="417" stroke="var(--white)" stroke-width="1.5"/>

  <g class="service service-virtual">
    <circle cx="151" cy="514" r="83" fill="var(--chartreuse)" stroke="var(--white)" stroke-width="2" role="img" aria-label="Line icon of a reception desk with mail envelope and plant"/>
    <text class="service-label" x="261" y="502">VIRTUAL</text>
    <text class="service-label" x="261" y="545">OFFICES</text>
  </g>
  <line class="service-divider" x1="276" y1="611" x2="449" y2="611" stroke="var(--white)" stroke-width="1.5"/>

  <g class="service service-coworking">
    <circle cx="151" cy="705" r="83" fill="var(--chartreuse)" stroke="var(--white)" stroke-width="2" role="img" aria-label="Line icon of two people talking at a shared table"/>
    <text class="service-label" x="261" y="693" textLength="273" lengthAdjust="spacingAndGlyphs">COWORKING</text>
    <text class="service-label" x="261" y="736">LOUNGE</text>
  </g>

  <g class="wave-band">
    <path d="M0 757 C 90 810, 200 850, 330 845 C 430 840, 520 810, 600 800 L600 1000 L0 1000 Z" fill="var(--chartreuse)"/>
    <path d="M0 780 C 100 830, 220 860, 340 852 C 440 845, 520 822, 600 812 L600 1000 L0 1000 Z" fill="var(--white)"/>
    <path d="M0 795 C 90 835, 170 860, 270 866 C 380 870, 480 840, 600 830 L600 1000 L0 1000 Z" fill="var(--blue)"/>
    <path d="M380 870 C 470 860, 540 845, 600 838 L600 830 C 530 836, 460 850, 380 870 Z" fill="var(--chartreuse)"/>
  </g>

  <text class="phone-number" x="300" y="946" font-size="104" text-anchor="middle" textLength="506" lengthAdjust="spacingAndGlyphs">310.555.2417</text>
</svg>
</body>
</html>
```